Postcard Design

We need a postcard to promote an upcoming event. We are an independent Montessori preschool and elementary school kicking off our 2015-16 Parent Education Series with a dynamic speaker Margaret Vollen-Price, 6:30 p.m. Wednesday, November 18th.
The design should get parents of both preschool children and elementary children to want to attend this event!
They should feel that they will really be missing out on a compelling and informative evening if they do not come.

Good to include some logo icons from media and publications that have featured her work (all these are on her web site)

Points to include:
Critical information for parents from birth through middle school on impact of technology on children and families, how to manage and incorporate technology in the healthiest way, how much is too much? how to be a GO-TO parent in the digital age...

Here is the website for the speaker: http://margaretvollenprice.example/

```html
<!DOCTYPE html>
<html lang="en">
<head>
<meta charset="utf-8">
<title>Parent Education Series Postcard</title>
<link rel="stylesheet" href="https://fonts.googleapis.com/css2?family=Libre+Baskerville:ital,wght@0,400;0,700;1,400;1,700&family=Open+Sans:ital,wght@0,400;0,600;0,700;1,400;1,600&display=swap">
<style>
  :root {
    --board: #8a5a36;
    --teal-dark: #1c5a69;
    --teal: #2f8593;
    --teal-light: #8fd0d6;
    --teal-pale: #e6f3f4;
    --ink-teal: #1f6676;
    --white: #ffffff;
    --muted: #9aa3a6;
    --orange: #f39a1e;
    --photo: #8f8a86;
    --book: #4a8fb0;
  }
  * { box-sizing: border-box; margin: 0; padding: 0; }
  html, body { width: 861px; height: 1200px; overflow: hidden; }
  body {
    background: var(--board);
    font-family: "Open Sans", sans-serif;
    position: relative;
  }
  .card { position: absolute; left: 28px; width: 805px; background: var(--white); overflow: hidden; box-shadow: 0 2px 6px rgba(0,0,0,.35); }

  /* front */
  .front { top: 22px; height: 575px; }
  .front-header { position: absolute; left: 0; top: 0; width: 100%; height: 118px; background: var(--teal-dark); padding: 16px 36px; }
  .speaker-name-caps { font-family: "Libre Baskerville", serif; color: var(--white); font-size: 40px; letter-spacing: 1px; text-transform: uppercase; white-space: nowrap; }
  .speaker-name-caps small { font-size: 16px; letter-spacing: 0; text-transform: none; }
  .speaker-roles { color: var(--teal-light); font-size: 19px; letter-spacing: 2.5px; margin-top: 6px; font-family: "Libre Baskerville", serif; white-space: nowrap; }
  .date-strip { position: absolute; left: 0; top: 118px; width: 100%; height: 46px; background: var(--teal); color: var(--white); font-weight: 700; font-size: 22px; padding: 8px 36px; }
  .front-main { position: absolute; left: 0; top: 164px; width: 100%; height: 358px; background: linear-gradient(#ffffff, var(--teal-pale)); }
  .speaker-name { position: absolute; left: 36px; top: 12px; font-family: "Libre Baskerville", serif; font-style: italic; font-weight: 700; color: var(--ink-teal); font-size: 31px; white-space: nowrap; }
  .speaker-name small { font-size: 17px; }
  .speaker-roles-line { position: absolute; left: 38px; top: 56px; font-style: italic; font-weight: 600; color: var(--ink-teal); font-size: 14px; }
  .speaker-photo { position: absolute; left: 38px; top: 88px; width: 180px; height: 222px; background: linear-gradient(160deg, #b5aea8, var(--photo)); border: 3px solid var(--white); }
  .event-headline { position: absolute; left: 240px; top: 90px; width: 330px; color: var(--ink-teal); font-weight: 700; font-size: 17.5px; line-height: 1.3; }
  .event-points { position: absolute; left: 240px; top: 192px; width: 330px; color: var(--ink-teal); font-style: italic; font-size: 13px; line-height: 1.5; }
  .school-panel { position: absolute; left: 592px; top: 12px; width: 185px; height: 300px; background: var(--white); border: 1px solid #cfe3e5; }
  .school-logo { display: flex; align-items: center; gap: 8px; padding: 14px 12px 0; color: var(--ink-teal); font-weight: 700; font-size: 17px; line-height: 1.15; }
  .school-logo .mark { width: 16px; height: 16px; background: var(--teal); border-radius: 50%; flex: none; }
  .book-cover { position: absolute; left: 14px; top: 84px; width: 155px; height: 200px; background: linear-gradient(160deg, #7fc1d6, var(--book)); }
  .front-footer { position: absolute; left: 0; bottom: 0; width: 100%; height: 53px; background: var(--teal); color: var(--white); font-style: italic; font-weight: 600; font-size: 18px; padding: 13px 36px; white-space: nowrap; }

  /* back */
  .back { top: 612px; height: 565px; background: var(--teal-pale); }
  .location-box { position: absolute; left: 34px; top: 26px; width: 250px; height: 200px; background: var(--white); border: 2px solid #d3dfe1; color: var(--muted); font-size: 20px; padding: 16px; }
  .call-band { position: absolute; left: 0; top: 240px; width: 305px; height: 58px; background: var(--teal); color: var(--white); font-weight: 700; font-size: 24px; padding: 13px 34px; }
  .office-details { position: absolute; left: 34px; top: 318px; width: 262px; color: var(--ink-teal); font-size: 12.5px; line-height: 1.55; }
  .office-site { position: absolute; left: 34px; top: 478px; color: var(--ink-teal); font-weight: 700; font-size: 13px; }
  .bio-panel { position: absolute; left: 320px; top: 20px; width: 466px; height: 318px; background: var(--teal-dark); color: var(--white); padding: 20px 22px; }
  .bio-panel .speaker-name-caps { font-size: 23px; letter-spacing: .5px; }
  .bio-panel .speaker-name-caps small { font-size: 12px; }
  .bio-panel .speaker-roles { font-size: 11px; letter-spacing: 1.5px; margin-top: 4px; }
  .bio-text { margin-top: 22px; font-style: italic; font-size: 15px; line-height: 1.6; }
  .ticket-box { position: absolute; left: 320px; top: 358px; width: 466px; height: 180px; background: var(--teal-light); padding: 18px 22px; color: var(--teal-dark); }
  .ticket-title { font-weight: 700; font-size: 27px; }
  .ticket-cta { font-size: 22px; margin-top: 8px; }
  .ticket-site { position: absolute; left: 22px; bottom: 16px; font-size: 13px; font-weight: 700; color: var(--white); }
  .price-badge { position: absolute; right: 26px; top: 18px; width: 112px; height: 112px; border-radius: 50%; background: var(--orange); border: 4px solid var(--white); color: var(--white); font-weight: 700; font-size: 38px; display: flex; align-items: center; justify-content: center; }
</style>
</head>
<body>

<section class="card front">
  <header class="front-header">
    <div class="speaker-name-caps">Margaret Vollen-Price <small>Ed.D.</small></div>
    <div class="speaker-roles">Clinical Psychologist, Consultant, Author, Speaker</div>
  </header>
  <div class="date-strip">6:30 p.m. Wednesday, November 18th</div>
  <div class="front-main">
    <div class="speaker-name">Margaret Vollen-Price <small>Ed.D.</small></div>
    <div class="speaker-roles-line">Clinical Psychologist, Consultant, Author, Speaker</div>
    <div class="speaker-photo" role="img" aria-label="Portrait photograph of the speaker"></div>
    <h2 class="event-headline">Independent Montessori Preschool and Elementary School Kicking Off our 2015-16 Parent Education Series</h2>
    <p class="event-points">Critical information for parents from birth through middle school on impact of technology on children and families, how to manage and incorporate technology in the healthiest way, how much is too much? how to be a GO-TO parent in the digital age...</p>
    <div class="school-panel">
      <div class="school-logo"><span class="mark"></span><span>Brookside Montessori</span></div>
      <div class="book-cover" role="img" aria-label="Cover of the speaker's book, The Screen Divide"></div>
    </div>
  </div>
  <footer class="front-footer">The Screen Divide: Keeping Families Close in a Connected World</footer>
</section>

<section class="card back">
  <div class="location-box">location directions</div>
  <div class="call-band">Call: 555-214-7780</div>
  <div class="office-details">
    Clinical and Consulting Psychologist<br>
    18 Linden Way, Fairview MA 01234<br>
    Email: office@margaretvollenprice.example<br>
    Phone: 555-214-7780
  </div>
  <div class="office-site">www.margaretvollenprice.example</div>

  <div class="bio-panel">
    <div class="speaker-name-caps">Margaret Vollen-Price <small>Ed.D.</small></div>
    <div class="speaker-roles">Clinical Psychologist, Consultant, Author, Speaker</div>
    <p class="bio-text">Writer of the much-praised guide The Screen Divide: Keeping Families Close in a Connected World, Dr. Vollen-Price looks at how screens and media shape the way young people think, play and connect, and gives parents clear, practical steps to enjoy what devices offer while guarding children at each age and stage.</p>
  </div>

  <div class="ticket-box">
    <div class="ticket-title">Ticket Reservation</div>
    <div class="ticket-cta">Book your ticket<br>Online......</div>
    <div class="ticket-site">www.margaretvollenprice.example</div>
    <div class="price-badge">$00</div>
  </div>
</section>

</body>
</html>
```